Veldmark Supplies Business Card

Professional business card that stand out to our potential customers. Front and back with clean modern design

Industry/Entity Type

Oil and gas

Contact Information for Business Card

Name, address, website , office phone and cell number

Requirements
Must have
• Editable files for each employee

```html
<!DOCTYPE html>
<html lang="en">
<head>
<meta charset="utf-8">
<title>Veldmark Supplies Business Card</title>
<link rel="stylesheet" href="https://fonts.googleapis.com/css2?family=Michroma&family=Montserrat:wght@500;600;800&display=swap">
<style>
  :root {
    --bg: #e3e3e3;
    --navy: #222a35;
    --paper: #ececec;
    --red: #dc2f36;
    --blue: #22a8c8;
    --ink: #2a2a2a;
    --white: #ffffff;
  }
  * { box-sizing: border-box; margin: 0; padding: 0; }
  html, body { width: 1200px; height: 675px; overflow: hidden; }
  body {
    background: var(--bg);
    font-family: "Montserrat", sans-serif;
    display: flex;
    align-items: center;
    justify-content: center;
    gap: 40px;
  }
  .card {
    position: relative;
    width: 540px;
    height: 309px;
    overflow: hidden;
    box-shadow: 0 10px 24px rgba(0,0,0,0.12);
  }
  .card--back { background: var(--navy); }
  .card--front { background: var(--paper); }

  .strip-top {
    position: absolute; top: 0; left: 0; right: 0;
    height: 7px; background: var(--red);
  }
  .band-bottom {
    position: absolute; bottom: 0; left: 0; right: 0;
    height: 18px; background: var(--red);
  }
  .band-tab {
    position: absolute; bottom: 17px; left: 33%; width: 34%;
    height: 16px; background: var(--red);
    border-radius: 6px 6px 0 0;
  }
  .card--back .band-tab {
    left: 33%;
    display: flex; align-items: center; justify-content: center;
    height: 24px; bottom: 10px;
  }
  .tab-url {
    color: var(--white);
    font-size: 11px;
    font-weight: 500;
    letter-spacing: 0.2px;
  }

  /* back: company name */
  .brand {
    position: absolute; top: 50%; left: 50%;
    transform: translate(-50%, -60%);
    display: flex; align-items: center; gap: 14px;
  }
  .brand-square {
    width: 34px; height: 34px; background: var(--red);
  }
  .brand-name {
    color: var(--white);
    font-weight: 800;
    font-size: 30px;
    letter-spacing: 1px;
    text-transform: uppercase;
    white-space: nowrap;
  }

  /* front */
  .front-brand {
    position: absolute; top: 58px; left: 30px;
    width: 190px;
    display: flex; flex-direction: column; align-items: flex-start; gap: 10px;
  }
  .front-brand .brand-square { width: 40px; height: 40px; }
  .front-brand .brand-name {
    color: var(--red);
    font-size: 24px;
    line-height: 1.1;
    white-space: normal;
  }
  .details {
    position: absolute; top: 48px; left: 236px; right: 20px;
  }
  .person-name {
    font-family: "Michroma", sans-serif;
    color: var(--blue);
    font-size: 17px;
    letter-spacing: 0.5px;
    text-transform: uppercase;
    white-space: nowrap;
  }
  .person-title {
    color: var(--ink);
    font-size: 11px;
    font-weight: 500;
    margin: 4px 0 14px;
  }
  .contacts { list-style: none; display: flex; flex-direction: column; gap: 9px; }
  .contact {
    display: flex; align-items: flex-start; gap: 10px;
    color: var(--ink); font-size: 12px; font-weight: 500; line-height: 1.3;
  }
  .contact-icon {
    flex: none; width: 18px; height: 18px; border-radius: 50%;
    background: var(--blue);
    display: flex; align-items: center; justify-content: center;
  }
  .contact-icon svg { width: 11px; height: 11px; }
</style>
</head>
<body>

  <section class="card card--back" aria-label="Business card back">
    <div class="strip-top"></div>
    <div class="brand">
      <span class="brand-square"></span>
      <span class="brand-name">Veldmark Supplies</span>
    </div>
    <div class="band-bottom"></div>
    <div class="band-tab"><span class="tab-url">www.veldmarksupplies.com</span></div>
  </section>

  <section class="card card--front" aria-label="Business card front">
    <div class="strip-top"></div>
    <div class="front-brand">
      <span class="brand-square"></span>
      <span class="brand-name">Veldmark Supplies</span>
    </div>
    <div class="details">
      <h1 class="person-name">Daniel Hartwell</h1>
      <p class="person-title">Marketing Manager</p>
      <ul class="contacts">
        <li class="contact">
          <span class="contact-icon"><svg viewBox="0 0 24 24" fill="#fff"><path d="M6.6 10.8a15 15 0 0 0 6.6 6.6l2.2-2.2a1 1 0 0 1 1-.25 11.4 11.4 0 0 0 3.6.57 1 1 0 0 1 1 1V20a1 1 0 0 1-1 1A17 17 0 0 1 3 4a1 1 0 0 1 1-1h3.5a1 1 0 0 1 1 1c0 1.25.2 2.45.57 3.57a1 1 0 0 1-.25 1z"/></svg></span>
          <span>(555)014-2287</span>
        </li>
        <li class="contact">
          <span class="contact-icon"><svg viewBox="0 0 24 24" fill="none" stroke="#fff" stroke-width="2"><rect x="3" y="6" width="18" height="12"/><path d="M3 6l9 7 9-7"/></svg></span>
          <span>sales@veldmarksupplies.com</span>
        </li>
        <li class="contact">
          <span class="contact-icon"><svg viewBox="0 0 24 24" fill="none" stroke="#fff" stroke-width="2"><circle cx="12" cy="12" r="9"/><path d="M3 12h18M12 3c3 3 3 15 0 18M12 3c-3 3-3 15 0 18"/></svg></span>
          <span>www.veldmarksupplies.com</span>
        </li>
        <li class="contact">
          <span class="contact-icon"><svg viewBox="0 0 24 24" fill="#fff"><path d="M12 2a7 7 0 0 0-7 7c0 5 7 13 7 13s7-8 7-13a7 7 0 0 0-7-7zm0 9.5A2.5 2.5 0 1 1 12 6.5a2.5 2.5 0 0 1 0 5z"/></svg></span>
          <span>622 W.Harlow Ave Suite 2<br>Crane Flats, Tx 79000</span>
        </li>
      </ul>
    </div>
    <div class="band-bottom"></div>
    <div class="band-tab"></div>
  </section>

</body>
</html>
```